Business Card for a Creative Technology based HR services company

Our company name is Lumo8, and we build large communities of HR (human resource) and finance personnels through our mobile platform, and we conduct lots of on-line and off-line activities to get everyone constantly connected. Behind all these, we will also provide on-site HR and finance contractors to our clients, plus a host of other HR-related services. No process in our company takes more than 5-steps.
Our company slogan: Touching Your Future
Target Market(s)
All human resource (HR) and finance personnels, from new entrants to highly experienced senior professionals.
Industry/Entity Type
Finance
Colors
Designer to choose colors to be used in the design.
Look and feel
Each slider illustrates characteristics of the customer's brand and the style your logo design should communicate.

```html
<!DOCTYPE html>
<html lang="en">
<head>
<meta charset="utf-8">
<title>Lumo8 Business Card</title>
<link rel="stylesheet" href="https://fonts.googleapis.com/css2?family=Open+Sans:wght@400;600;700&display=swap">
<style>
  :root {
    --navy: #0d2a54;
    --red: #e3151f;
    --white: #ffffff;
    --grey-text: #3d3d3d;
    --backdrop: #e9e9ea;
  }
  * { margin: 0; padding: 0; box-sizing: border-box; }
  html, body {
    width: 1200px; height: 900px; overflow: hidden;
    background: var(--backdrop);
    font-family: "Open Sans", Arial, sans-serif;
  }
  .card {
    position: absolute; left: 100px; top: 160px;
    width: 1000px; height: 580px;
    filter: drop-shadow(0 10px 24px rgba(0,0,0,0.18));
  }
  .card-art { position: absolute; inset: 0; }
  .brand-name {
    position: absolute; left: 80px; top: 192px;
    font-size: 64px; font-weight: 600; color: var(--navy);
    line-height: 1;
  }
  .person {
    position: absolute; right: 258px; top: 250px; text-align: right;
  }
  .person-name { font-size: 28px; font-weight: 700; color: var(--red); line-height: 1.2; }
  .person-role { font-size: 26px; font-weight: 400; color: var(--grey-text); line-height: 1.3; }
  .contact {
    position: absolute; left: 80px; top: 418px;
    color: var(--white); font-size: 19px; line-height: 1.35;
  }
  .contact-phones { margin-bottom: 12px; }
</style>
</head>
<body>
  <div class="card">
    <svg class="card-art" width="1000" height="580" viewBox="0 0 1000 580" aria-hidden="true">
      <defs>
        <clipPath id="card-shape">
          <path d="M24,110 H188 Q214,110 218,84 L224,26 Q228,0 254,0 H976 Q1000,0 1000,24 V556 Q1000,580 976,580 H24 Q0,580 0,556 V134 Q0,110 24,110 Z"/>
        </clipPath>
      </defs>
      <g clip-path="url(#card-shape)">
        <rect class="card-face" width="1000" height="580" fill="var(--white)"/>
        <path class="card-band" d="M0,362 C320,452 720,452 862,347 C942,282 982,152 1000,92 V580 H0 Z" fill="var(--navy)"/>
        <path class="card-swoosh" d="M90,352 C380,432 700,430 835,330 C905,270 930,150 898,40 C950,130 945,270 866,338 C730,448 380,446 90,352 Z" fill="var(--red)"/>
      </g>
    </svg>

    <p class="brand-name">Lumo8</p>

    <div class="person">
      <p class="person-name">Maren Holt-Avery</p>
      <p class="person-role">Consultant</p>
    </div>

    <div class="contact">
      <div class="contact-phones">
        <p>P : 021 555 0147</p>
        <p>F : 021 555 0147</p>
      </div>
      <p>hello@lumo8mail.com</p>
      <p>www.lumo8hub.com</p>
      <p>27, 9th floor, Harbor Line Road KTP</p>
    </div>
  </div>
</body>
</html>
```